SkyvornQ Business Cards and Stationary Design

Need a design for our business cards and stationary. I want to carry on the theme of the logo. I want the business cards to have a design on the back. I would like the business cards and the stationary to carry the same theme, design scheme, and branding

Target Market(s)

Airlines and Maintenance Facilities

Industry/Entity Type

Aviation

Contact Information for Business Card

Name
Position Title
Address: 4827 Trellis Hollow Road, Fort Pierce, Florida, 34951
Office Number
Mobile Number
Email
Website

Font styles to use
Serif
Sans Serif

Colors

Designer to choose colors to be used in the design.

```html
<!DOCTYPE html>
<html lang="en">
<head>
<meta charset="utf-8">
<title>SkyvornQ Business Card</title>
<link rel="stylesheet" href="https://fonts.googleapis.com/css2?family=Montserrat:wght@400;500;700;800&display=swap">
<style>
  :root {
    --bg: #2b2b2e;
    --sky-blue: #2a8fcb;
    --mid-blue: #2f5f9e;
    --deep-violet: #33277a;
    --violet: #36287e;
    --band: #3b3b3f;
    --white: #ffffff;
    --soft-white: #e4e2f2;
  }
  * { margin: 0; padding: 0; box-sizing: border-box; }
  html, body {
    width: 1200px; height: 900px; overflow: hidden;
    background: var(--bg);
    font-family: "Montserrat", Arial, sans-serif;
    color: var(--white);
  }
  .stage { position: relative; width: 1200px; height: 900px; }
  .card {
    position: absolute;
    width: 600px; height: 343px;
    border-radius: 18px;
    overflow: hidden;
    box-shadow: 0 18px 40px rgba(0,0,0,0.45);
  }
  .card-front {
    left: 70px; top: 70px;
    background: linear-gradient(35deg, var(--sky-blue) 0%, var(--mid-blue) 40%, var(--deep-violet) 72%, var(--violet) 100%);
  }
  .front-brand {
    position: absolute; left: 0; right: 0; top: 112px;
    display: flex; flex-direction: column; align-items: center;
  }
  .brand-row { display: flex; align-items: center; gap: 18px; }
  .brand-dot {
    width: 44px; height: 44px; border-radius: 50%;
    border: 5px solid var(--white);
  }
  .brand-name {
    font-weight: 800; font-size: 46px; letter-spacing: 9px;
    text-transform: uppercase;
  }
  .front-web {
    margin-top: 26px; font-size: 14px; font-weight: 500; letter-spacing: 0.5px;
  }

  .card-back {
    left: 530px; top: 487px;
    background: var(--violet);
  }
  .back-panel {
    position: absolute; left: 0; top: 0; bottom: 0; width: 300px;
    background: linear-gradient(40deg, var(--sky-blue) 0%, var(--mid-blue) 55%, var(--deep-violet) 100%);
  }
  .back-brand {
    position: absolute; left: 0; width: 300px; top: 142px;
    display: flex; align-items: center; justify-content: center; gap: 10px;
  }
  .back-brand .brand-dot { width: 30px; height: 30px; border-width: 4px; }
  .back-brand .brand-name { font-size: 30px; letter-spacing: 5px; }
  .band-tab {
    position: absolute; left: 285px; top: 0; width: 52px; height: 78px;
    background: var(--band); border-radius: 0 0 26px 26px;
  }
  .band-icons {
    position: absolute; left: 285px; top: 128px; bottom: 0; width: 52px;
    background: var(--band); border-radius: 26px 26px 0 0;
    display: flex; flex-direction: column; align-items: center;
    padding-top: 22px; gap: 26px;
  }
  .band-icons svg { width: 22px; height: 22px; display: block; }
  .holder {
    position: absolute; left: 362px; top: 40px;
  }
  .holder-name { font-size: 25px; font-weight: 700; letter-spacing: 1.5px; text-transform: uppercase; }
  .holder-title { font-size: 13px; font-weight: 400; margin-top: 2px; color: var(--soft-white); }
  .contact-list {
    position: absolute; left: 362px; top: 150px;
    list-style: none; font-size: 15px; font-weight: 500;
  }
  .contact-list li { height: 48px; line-height: 22px; }
</style>
</head>
<body>
<main class="stage">
  <section class="card card-front">
    <div class="front-brand">
      <div class="brand-row">
        <span class="brand-dot"></span>
        <span class="brand-name">SkyvornQ</span>
      </div>
      <p class="front-web">www.skyvornq.com</p>
    </div>
  </section>

  <section class="card card-back">
    <div class="back-panel"></div>
    <div class="back-brand">
      <span class="brand-dot"></span>
      <span class="brand-name">SkyvornQ</span>
    </div>
    <div class="band-tab"></div>
    <div class="band-icons">
      <svg viewBox="0 0 24 24" fill="none" stroke="#fff" stroke-width="1.8" aria-label="Mobile"><rect x="6" y="2" width="12" height="20" rx="2"/><line x1="10" y1="18.5" x2="14" y2="18.5"/></svg>
      <svg viewBox="0 0 24 24" fill="#fff" aria-label="Office phone"><path d="M6.6 10.8a15 15 0 0 0 6.6 6.6l2.2-2.2a1 1 0 0 1 1-.25 11.4 11.4 0 0 0 3.6.57 1 1 0 0 1 1 1V20a1 1 0 0 1-1 1A17 17 0 0 1 3 4a1 1 0 0 1 1-1h3.5a1 1 0 0 1 1 1c0 1.25.2 2.45.57 3.57a1 1 0 0 1-.25 1z"/></svg>
      <svg viewBox="0 0 24 24" fill="none" stroke="#fff" stroke-width="1.8" aria-label="Email"><rect x="3" y="5" width="18" height="14" rx="1.5"/><polyline points="3,6 12,13 21,6"/></svg>
      <svg viewBox="0 0 24 24" fill="none" stroke="#fff" stroke-width="1.5" aria-label="Website"><circle cx="12" cy="12" r="9"/><ellipse cx="12" cy="12" rx="4" ry="9"/><line x1="3" y1="12" x2="21" y2="12"/><line x1="5" y1="7" x2="19" y2="7"/><line x1="5" y1="17" x2="19" y2="17"/></svg>
    </div>
    <div class="holder">
      <h1 class="holder-name">Dana Whitlock</h1>
      <p class="holder-title">CEO/ Founder</p>
    </div>
    <ul class="contact-list">
      <li>(760) 555-0148</li>
      <li>1-833-555-0172</li>
      <li>info@skyvornq.com</li>
      <li>www.skyvornq.com</li>
    </ul>
  </section>
</main>
</body>
</html>
```